Property maintenance company needs an eye catching postcard design

We are a property maintenance company that wants to send out a postcard targeting residential homeowners only. We want the postcard to create the impression of a friendly and inviting company that makes maintenance easy for homeowners. I have attached all the instructions in a pdf file as well as any other needed pictures or info. Please read the outline I provided. I also attached pictures/screenshots of our new (in progress) website if you wish to get a feel for our company.

Thanks!

Target Market(s)

residential homeowners, homeowners

Industry/Entity Type

Property Maintenance

```html
<!DOCTYPE html>
<html lang="en">
<head>
<meta charset="utf-8">
<title>TruePoint Postcard</title>
<link href="https://fonts.googleapis.com/css2?family=Arimo:wght@400;700&family=Montserrat:wght@700;800&display=swap" rel="stylesheet">
<style>
  :root {
    --navy: #2f2a7c;
    --indigo: #3f3f9a;
    --periwinkle: #5f77bb;
    --accent-blue: #3f55b0;
    --green: #7ac143;
    --white: #ffffff;
    --backdrop: #e9e5df;
    --line: #e4e4e4;
    --stamp: #ececec;
  }
  * { box-sizing: border-box; margin: 0; padding: 0; }
  html, body { width: 1200px; height: 1200px; overflow: hidden; }
  body { background: var(--backdrop); position: relative; font-family: "Arimo", Arial, sans-serif; }

  .postcard { position: absolute; left: 224px; width: 752px; height: 500px; overflow: hidden; box-shadow: 0 4px 14px rgba(0,0,0,.18); background: var(--white); }
  .postcard--front { top: 98px; }
  .postcard--back { top: 633px; }

  .abs { position: absolute; }

  /* front */
  .hero-photo { position: absolute; inset: 0; width: 100%; height: 100%; }
  .brand { display: flex; align-items: center; gap: 8px; }
  .brand-square { width: 14px; height: 14px; background: var(--indigo); }
  .brand-name { font-family: "Arimo", Arial, sans-serif; font-weight: 700; color: var(--indigo); letter-spacing: .5px; }
  .front-brand { left: 43px; top: 90px; }
  .front-brand .brand-name { font-size: 30px; }

  .headline { left: 42px; top: 178px; }
  .headline-name { font-family: "Arimo", Arial, sans-serif; font-weight: 700; color: var(--green); font-size: 56px; line-height: 54px; letter-spacing: -3px; }
  .headline-sub { font-family: "Arimo", Arial, sans-serif; font-weight: 400; color: var(--navy); font-size: 38px; line-height: 37px; letter-spacing: -1px; }
  .headline-rule { left: 43px; top: 322px; width: 68px; height: 5px; background: var(--accent-blue); }
  .tagline { left: 43px; top: 344px; font-family: "Montserrat", Arial, sans-serif; font-weight: 700; font-size: 15px; line-height: 20px; color: var(--accent-blue); letter-spacing: .4px; }

  .front-band { left: 0; bottom: 0; width: 752px; height: 100px; }
  .contact-item { display: flex; align-items: center; gap: 6px; color: var(--white); font-size: 12.5px; }
  .contact-icon { width: 20px; height: 20px; flex: none; }
  .front-contacts { top: 457px; }

  /* back */
  .info-panel { left: 0; top: 0; width: 376px; height: 500px; }
  .section-tag { height: 29px; }
  .tag-do { left: 80px; top: 49px; width: 206px; }
  .tag-offer { left: 61px; top: 205px; width: 245px; }
  .tag-label { position: absolute; left: 0; top: 0; width: 100%; height: 29px; display: flex; align-items: center; justify-content: center; font-family: "Montserrat", Arial, sans-serif; font-weight: 800; font-size: 20px; color: var(--white); letter-spacing: 1px; }

  .service-list { left: 0; top: 92px; width: 376px; list-style: none; text-align: center; color: var(--white); font-size: 13.5px; }
  .service-list li { height: 23.5px; display: flex; align-items: center; justify-content: center; gap: 5px; }
  .tick { width: 12px; height: 12px; flex: none; }

  .offer-list { left: 10px; top: 266px; width: 356px; display: flex; justify-content: space-between; color: var(--white); font-size: 13.5px; }
  .offer { width: 68px; display: flex; flex-direction: column; align-items: center; gap: 9px; }
  .offer svg { width: 26px; height: 26px; }

  .back-brand { left: 0; top: 398px; width: 376px; justify-content: center; }
  .back-brand .brand-name { font-size: 26px; }
  .back-contacts { left: 24px; top: 461px; display: flex; gap: 16px; }
  .back-contacts .contact-item { color: #222; font-size: 14px; letter-spacing: .4px; }

  .stamp-box { left: 629px; top: 42px; width: 81px; height: 91px; background: var(--stamp); }
  .address-line { left: 407px; width: 306px; height: 1px; background: var(--line); }
  .listing-badge { left: 657px; top: 443px; width: 56px; height: 21px; background: #1d5f99; border-radius: 2px; }
</style>
</head>
<body>

<section class="postcard postcard--front">
  <svg class="hero-photo" viewBox="0 0 752 500" role="img" aria-label="Photo of a handyman's tool belt with tape measure, gloves and tools in front of a bright home entrance">
    <defs>
      <linearGradient id="heroFade" x1="0" y1="0" x2="1" y2="0">
        <stop offset="0" stop-color="#f3f3f3"/>
        <stop offset=".45" stop-color="#e9ebee"/>
        <stop offset=".62" stop-color="#a9b7cc"/>
        <stop offset=".8" stop-color="#5d74a0"/>
        <stop offset="1" stop-color="#3a4a7c"/>
      </linearGradient>
    </defs>
    <rect width="752" height="500" fill="url(#heroFade)"/>
  </svg>

  <div class="abs brand front-brand"><span class="brand-square"></span><span class="brand-name">TruePoint Services</span></div>

  <h1 class="abs headline">
    <span class="headline-name">TRUEPOINT</span><br>
    <span class="headline-sub">MAKES HOME<br>MAINTENANCE EASY</span>
  </h1>
  <div class="abs headline-rule"></div>
  <p class="abs tagline">ONE POINT OF CONTACT FOR ALL YOUR<br>PROPERTY MAINTENANCE NEEDS</p>

  <svg class="abs front-band" viewBox="0 0 752 100" preserveAspectRatio="none">
    <path d="M0 86 Q 376 -45 752 86 L752 100 L0 100 Z" fill="var(--green)"/>
    <path d="M0 93 Q 376 -30 752 93 L752 100 L0 100 Z" fill="var(--navy)"/>
  </svg>

  <div class="abs contact-item front-contacts" style="left:153px">
    <svg class="contact-icon" viewBox="0 0 20 20"><circle cx="10" cy="10" r="10" fill="var(--green)"/><path d="M7 5 L9 8 L8 9 Q9 11.5 11 12 L12 11 L15 13 L14 15 Q8 15 5 8 Z" fill="#fff"/></svg>
    <span>403-555-0142</span>
  </div>
  <div class="abs contact-item front-contacts" style="left:288px">
    <svg class="contact-icon" viewBox="0 0 20 20"><circle cx="10" cy="10" r="10" fill="var(--green)"/><rect x="5" y="6.5" width="10" height="7" fill="none" stroke="#fff" stroke-width="1.2"/><path d="M5 6.5 L10 10.5 L15 6.5" fill="none" stroke="#fff" stroke-width="1.2"/></svg>
    <span>info@truepointhome.com</span>
  </div>
  <div class="abs contact-item front-contacts" style="left:478px">
    <svg class="contact-icon" viewBox="0 0 20 20"><circle cx="10" cy="10" r="10" fill="var(--green)"/><circle cx="10" cy="10" r="5" fill="none" stroke="#fff" stroke-width="1.2"/><path d="M5 10 H15 M10 5 Q7 10 10 15 M10 5 Q13 10 10 15" fill="none" stroke="#fff" stroke-width="1.1"/></svg>
    <span>www.truepointhome.com</span>
  </div>
</section>

<section class="postcard postcard--back">
  <svg class="abs info-panel" viewBox="0 0 376 500" preserveAspectRatio="none">
    <defs>
      <linearGradient id="panelFade" x1="0" y1="0" x2="0" y2="1">
        <stop offset="0" stop-color="var(--periwinkle)"/>
        <stop offset=".75" stop-color="var(--navy)"/>
      </linearGradient>
    </defs>
    <rect width="376" height="500" fill="url(#panelFade)"/>
    <path d="M0 407 Q 188 290 376 407 L376 500 L0 500 Z" fill="var(--green)"/>
    <path d="M0 414 Q 188 303 376 414 L376 500 L0 500 Z" fill="var(--white)"/>
  </svg>

  <div class="abs section-tag tag-do">
    <svg width="206" height="29" viewBox="0 0 206 29"><path d="M8 0 H14 L6 29 H0 Z M18 0 H188 L180 29 H10 Z M192 0 H198 L190 29 H184 Z M202 0 H206 L198 29 H194 Z" fill="var(--green)"/></svg>
    <span class="tag-label">WHAT WE DO</span>
  </div>
  <ul class="abs service-list">
    <li><svg class="tick" viewBox="0 0 12 12"><circle cx="6" cy="6" r="6" fill="var(--green)"/><path d="M3 6 L5.2 8 L9 4" fill="none" stroke="#fff" stroke-width="1.5"/></svg>Maintenance Packages</li>
    <li><svg class="tick" viewBox="0 0 12 12"><circle cx="6" cy="6" r="6" fill="var(--green)"/><path d="M3 6 L5.2 8 L9 4" fill="none" stroke="#fff" stroke-width="1.5"/></svg>General Maintenance/Handyman Repairs</li>
    <li><svg class="tick" viewBox="0 0 12 12"><circle cx="6" cy="6" r="6" fill="var(--green)"/><path d="M3 6 L5.2 8 L9 4" fill="none" stroke="#fff" stroke-width="1.5"/></svg>Home Renovations</li>
  </ul>

  <div class="abs section-tag tag-offer">
    <svg width="245" height="29" viewBox="0 0 245 29"><path d="M8 0 H14 L6 29 H0 Z M18 0 H227 L219 29 H10 Z M231 0 H237 L229 29 H223 Z M241 0 H245 L237 29 H233 Z" fill="var(--green)"/></svg>
    <span class="tag-label">WHAT WE OFFER</span>
  </div>

  <div class="abs offer-list">
    <div class="offer">
      <svg viewBox="0 0 26 26"><path d="M6 2 V8 M12 2 V8 M3 8 H15 V13 Q15 17 9 17 Q3 17 3 13 Z M9 17 V22 Q9 24 13 24 Q20 24 20 16 V2" fill="none" stroke="var(--green)" stroke-width="2.2"/></svg>
      <span>Electrical</span>
    </div>
    <div class="offer">
      <svg viewBox="0 0 26 26"><path d="M3 24 V12 L9 15 V10 L15 14 V7 H20 V24 Z M5 2 L8 6 M10 2 L12 6" fill="var(--green)" stroke="var(--green)" stroke-width="1.5"/></svg>
      <span>Millwork</span>
    </div>
    <div class="offer">
      <svg viewBox="0 0 26 26"><path d="M3 2 V24 M8 2 V24 M13 2 V24 M18 2 V24 M23 2 V24 M1 9 H25 M1 17 H25" fill="none" stroke="var(--green)" stroke-width="1.3"/></svg>
      <span>Flooring</span>
    </div>
    <div class="offer">
      <svg viewBox="0 0 26 26"><path d="M2 6 H14 Q20 6 20 12 V20 M8 3 V9 M17 20 H23 V24 H17 Z" fill="none" stroke="var(--green)" stroke-width="2.2"/></svg>
      <span>Plumbing</span>
    </div>
    <div class="offer">
      <svg viewBox="0 0 26 26"><path d="M4 22 L20 6 M6 6 L22 22 M15 3 H24 V8 H15 Z M2 7 L7 2 L10 5 L5 10 Z" fill="var(--green)" stroke="var(--green)" stroke-width="2.4"/></svg>
      <span>Carpentry</span>
    </div>
  </div>

  <div class="abs brand back-brand"><span class="brand-square"></span><span class="brand-name">TruePoint Services</span></div>

  <div class="abs back-contacts">
    <div class="contact-item">
      <svg class="contact-icon" viewBox="0 0 20 20"><circle cx="10" cy="10" r="10" fill="var(--green)"/><path d="M7 5 L9 8 L8 9 Q9 11.5 11 12 L12 11 L15 13 L14 15 Q8 15 5 8 Z" fill="#fff"/></svg>
      <span>403-555-0142</span>
    </div>
    <div class="contact-item">
      <svg class="contact-icon" viewBox="0 0 20 20"><circle cx="10" cy="10" r="10" fill="var(--green)"/><rect x="5" y="6.5" width="10" height="7" fill="none" stroke="#fff" stroke-width="1.2"/><path d="M5 6.5 L10 10.5 L15 6.5" fill="none" stroke="#fff" stroke-width="1.2"/></svg>
      <span>www.truepointhome.com</span>
    </div>
  </div>

  <div class="abs stamp-box"></div>
  <div class="abs address-line" style="top:182px"></div>
  <div class="abs address-line" style="top:256px"></div>
  <div class="abs address-line" style="top:330px"></div>
  <div class="abs address-line" style="top:403px"></div>
  <div class="abs listing-badge"></div>
</section>

</body>
</html>
```